Business card design needed

Front of Card:
I would like to have nearly 3/4 of the card from the top in a Pea Green Colour with the word 'Brambleway' written in a(Watermelon Red colour) in the font 'Viner Hand ITC'. Brambleway to be written within the Green colour of the card.

The lower 1/3 of the card I would like to have white with the words:
Home and Garden Styling smaller than the word Brambleway in Black in the font 'Batang', centred underneath the green section.

At the very bottom in one corner in smaller print I would like to have my contact phone number: Pia M:0437619204 and then the email address:
E: brambleaystudio@kelnor.net.au on the other side.

Back of Card:
Back of Card to be White
On one side (Left)
I would like the Heading "Garden" in the same pea green colour as the front and in the Viner Hand ITC font. On the other half of the card I would like 'Home' in the Watermelon Red Colour (same as front colour) and in the font Viner Hand ITC.
Underneath these Headings I would like written in black and in Batang font the following list of services.

Garden Home
Garden Styling Interior Styling
Plant Selection Furniture Selection/Arrangement Garden Maintenance Setting Up Home (after move)
Hedging/Mowing Merchandise and Stylist for
Work w/Local Nurseries Marrow and Finch

Brambleway
Home and Garden Styling
M: 0437619204 E: brambleaystudio@kelnor.net.au

```html
<!DOCTYPE html>
<html lang="en">
<head>
<meta charset="utf-8">
<title>Brambleway – Business Card Concepts</title>
<link rel="stylesheet" href="https://fonts.googleapis.com/css2?family=Gowun+Batang:wght@400;700&family=Kaushan+Script&family=Arial&display=swap">
<style>
  :root {
    --pea-green: #217a3b;
    --watermelon: #e8344f;
    --heading-pink: #e02a63;
    --ink: #1e1e1e;
    --paper: #ffffff;
    --sheet: #ebeded;
    --card-edge: #d6d8d8;
    --label: #2a2a2a;
    --script: "Kaushan Script", cursive;
    --serif: "Gowun Batang", serif;
  }
  * { box-sizing: border-box; margin: 0; padding: 0; }
  html, body { width: 1200px; height: 631px; overflow: hidden; }
  body { background: var(--sheet); position: relative; font-family: var(--serif); color: var(--ink); }

  .sheet-label {
    position: absolute; font-family: Arial, Helvetica, sans-serif;
    font-size: 24px; color: var(--label); line-height: 1;
  }
  .sheet-label--big { font-size: 38px; }

  .card {
    position: absolute; width: 467px; height: 259px;
    background: var(--paper); border: 1px solid var(--card-edge);
    box-shadow: 0 1px 4px rgba(0,0,0,0.12); overflow: hidden;
  }

  /* Front */
  .front__field {
    position: absolute; left: 0; top: 0; width: 100%; height: 165px;
    background: var(--pea-green);
    display: flex; align-items: center; justify-content: center;
  }
  .front__name {
    font-family: var(--script); color: var(--watermelon);
    font-size: 76px; line-height: 1; margin-top: -10px; letter-spacing: 1px;
  }
  .front__tagline {
    position: absolute; left: 0; right: 0; top: 178px;
    text-align: center; font-size: 30px; letter-spacing: 0.5px;
  }
  .front__contact {
    position: absolute; top: 226px; font-size: 15px;
    display: flex; align-items: center; gap: 4px;
  }
  .front__contact--phone { left: 46px; }
  .front__contact--email { left: 180px; gap: 8px; }
  .front__contact svg { display: block; }

  /* Back */
  .back__heading {
    position: absolute; font-family: var(--script); font-size: 34px; line-height: 1;
  }
  .back__heading--garden { color: var(--pea-green); }
  .back__heading--home { color: var(--heading-pink); }

  .services { position: absolute; list-style: none; font-size: 13.5px; line-height: 20px; }
  .services li { position: relative; padding-left: 10px; white-space: nowrap; }
  .services li::before {
    content: ""; position: absolute; left: 0; top: 8px;
    width: 4px; height: 4px; border-radius: 50%;
  }
  .services--garden li::before { background: var(--pea-green); }
  .services--home li::before { background: var(--heading-pink); }
  .services li.services__continued::before { display: none; }

  .back__band { position: absolute; left: 0; width: 100%; }
  .band-green { fill: var(--pea-green); }
  .band-red { fill: var(--watermelon); }
</style>
</head>
<body>

  <span class="sheet-label sheet-label--big" style="left:36px; top:46px;">1</span>
  <span class="sheet-label" style="left:7px; top:343px;">back 1</span>
  <span class="sheet-label" style="left:601px; top:72px;">back 1a</span>
  <span class="sheet-label" style="left:596px; top:345px;">back 1b</span>

  <!-- Front -->
  <section class="card front" style="left:82px; top:47px;">
    <div class="front__field">
      <span class="front__name">Brambleway</span>
    </div>
    <p class="front__tagline">Home and Garden Styling</p>
    <p class="front__contact front__contact--phone">
      <svg width="11" height="14" viewBox="0 0 11 14" aria-hidden="true">
        <path d="M3 1 L5 4 L3.6 5.6 C4.2 7.6 5.4 9.2 7 10.2 L8.6 9 L10.4 11.6 L8.6 13 C4.4 12 1.2 7.6 1 2.4 Z" fill="none" stroke="#1e1e1e" stroke-width="1.3" stroke-linejoin="round"/>
      </svg>
      0437619204
    </p>
    <p class="front__contact front__contact--email">
      <svg width="16" height="11" viewBox="0 0 16 11" aria-hidden="true">
        <rect x="0.6" y="0.6" width="14.8" height="9.8" fill="none" stroke="#1e1e1e" stroke-width="1.1"/>
        <path d="M0.8 0.8 L8 6 L15.2 0.8" fill="none" stroke="#1e1e1e" stroke-width="1.1"/>
      </svg>
      brambleaystudio@kelnor.net.au
    </p>
  </section>

  <!-- Back 1 -->
  <section class="card back" style="left:85px; top:332px;">
    <h2 class="back__heading back__heading--garden" style="left:46px; top:38px;">Garden</h2>
    <h2 class="back__heading back__heading--home" style="left:254px; top:38px;">Home</h2>
    <ul class="services services--garden" style="left:41px; top:104px;">
      <li>Garden Styling</li><li>Plant Selection</li><li>Garden Maintenance</li>
      <li>Hedging/Mowing</li><li>Work w/Local Nurseries</li>
    </ul>
    <ul class="services services--home" style="left:233px; top:104px;">
      <li>Interior Styling</li><li>Furniture Selection/Arrangement</li>
      <li>Setting Up Home (after move)</li><li>Merchandise and Stylist</li>
      <li class="services__continued">for Marrow &amp; Finch</li>
    </ul>
    <svg class="back__band" style="top:242px;" width="467" height="17" viewBox="0 0 467 17" aria-hidden="true">
      <rect class="band-green" x="0" y="0" width="260" height="17"/>
      <polygon class="band-red" points="248,17 300,0 467,0 467,17"/>
    </svg>
  </section>

  <!-- Back 1a -->
  <section class="card back" style="left:700px; top:50px;">
    <h2 class="back__heading back__heading--garden" style="left:60px; top:26px;">Garden</h2>
    <h2 class="back__heading back__heading--home" style="left:303px; top:30px;">Home</h2>
    <svg class="back__band" style="top:68px;" width="467" height="21" viewBox="0 0 467 21" aria-hidden="true">
      <polygon class="band-green" points="0,0 252,0 216,15 0,15"/>
      <polygon class="band-red" points="216,21 241,5 467,5 467,21"/>
    </svg>
    <ul class="services services--garden" style="left:36px; top:128px;">
      <li>Garden Styling</li><li>Plant Selection</li><li>Garden Maintenance</li>
      <li>Hedging/Mowing</li><li>Work w/Local Nurseries</li>
    </ul>
    <ul class="services services--home" style="left:236px; top:130px;">
      <li>Interior Styling</li><li>Furniture Selection/Arrangement</li>
      <li>Setting Up Home (after move)</li><li>Merchandise and Stylist</li>
      <li class="services__continued">for Marrow &amp; Finch</li>
    </ul>
  </section>

  <!-- Back 1b -->
  <section class="card back" style="left:700px; top:328px;">
    <h2 class="back__heading back__heading--garden" style="left:60px; top:28px;">Garden</h2>
    <h2 class="back__heading back__heading--home" style="left:303px; top:32px;">Home</h2>
    <svg class="back__band" style="top:72px;" width="467" height="15" viewBox="0 0 467 15" aria-hidden="true">
      <rect class="band-green" x="0" y="0" width="260" height="15"/>
      <polygon class="band-red" points="244,15 268,0 467,0 467,15"/>
    </svg>
    <ul class="services services--garden" style="left:36px; top:128px;">
      <li>Garden Styling</li><li>Plant Selection</li><li>Garden Maintenance</li>
      <li>Hedging/Mowing</li><li>Work w/Local Nurseries</li>
    </ul>
    <ul class="services services--home" style="left:236px; top:130px;">
      <li>Interior Styling</li><li>Furniture Selection/Arrangement</li>
      <li>Setting Up Home (after move)</li><li>Merchandise and Stylist</li>
      <li class="services__continued">for Marrow &amp; Finch</li>
    </ul>
  </section>

</body>
</html>
```